Tarnell Pure Systems

I'm looking for a postcard design for large bulk mailers. We own a Whole Home Alkaline Purification Softening and Filtration Systems. 10X8 Postcard. I have attached my logo and our old postcard. You can get information off the www. quellarobrookguild website or our website www.tarnellpuresystems.com

• 15% off Coupon Code 3916 While Supplies Last. Can you put the postal info on there? You will see if on the flyer attached.
• Is Your Water Safe

```html
<!DOCTYPE html>
<html lang="en">
<head>
<meta charset="utf-8">
<title>Tarnell Pure Systems – Postcard</title>
<link href="https://fonts.googleapis.com/css2?family=Kanit:wght@300;400;500;600;700&family=Montserrat:wght@700;800&family=Poppins:wght@300;400;500;600;700;800&display=swap" rel="stylesheet">
<style>
:root{
  --stage:#111114;
  --navy:#1b3a6b;
  --deep:#0d4f8b;
  --mid:#1a8cc4;
  --sky:#eef8fd;
  --cyan:#6ef0fa;
  --orange:#f07f2a;
  --white:#ffffff;
}
*{margin:0;padding:0;box-sizing:border-box}
html,body{width:734px;height:1200px;overflow:hidden;background:var(--stage)}
body{position:relative;font-family:"Poppins",sans-serif}
.card{position:absolute;left:43px;width:652px;height:521px;overflow:hidden}
.card--front{top:43px}
.card--back{top:616px;background:var(--sky)}
.card svg.bg{position:absolute;inset:0}
.abs{position:absolute;white-space:nowrap}
.center{left:0;right:0;text-align:center}

/* front */
.brand-mark{position:absolute;left:276px;top:40px;width:100px;height:100px;border-radius:50%;background:var(--navy)}
.brand-name{top:181px;font-family:"Montserrat",sans-serif;font-weight:800;font-size:27px;letter-spacing:1px;color:var(--navy)}
.indicia{left:572px;top:18px;width:60px;height:78px;background:var(--white);border:1px solid #222;font-family:Arial,sans-serif;font-size:5.2px;line-height:6.4px;color:#111;text-align:center}
.indicia .top{padding:3px 1px;border-bottom:1px solid #222;height:43px}
.indicia .bottom{text-align:left;padding:3px 6px}
.headline{top:381px;font-family:"Montserrat",sans-serif;font-weight:800;font-size:48px;line-height:1;color:var(--cyan);letter-spacing:-.5px}
.intro{top:430px;font-size:9.4px;line-height:12.4px;font-weight:500;color:var(--white)}
.concerns{top:456px;font-size:21px;font-weight:700;color:var(--white);line-height:30px}
.rule{top:470px;height:3px;background:var(--cyan)}
.contact-row{top:484px;display:flex;justify-content:center;gap:18px;font-size:22px;font-weight:300;color:var(--white);line-height:28px}
.contact-row span{display:flex;align-items:center;gap:8px}

/* back */
.lead{left:22px;top:16px;font-family:"Kanit",sans-serif;font-size:26px;line-height:27.6px;font-weight:600;letter-spacing:-.3px;color:var(--cyan)}
.about-pill{left:0;top:146px;width:202px;height:37px;background:var(--white);border-radius:0 19px 19px 0;font-family:"Montserrat",sans-serif;font-weight:800;font-size:27px;color:var(--deep);padding-left:22px;line-height:38px}
.about-copy{left:21px;top:196px;font-size:9.4px;line-height:14.4px;font-weight:400;color:var(--white)}
.leader{left:22px;top:365px;font-family:"Kanit",sans-serif;font-size:12.8px;line-height:15.7px;font-weight:600;color:var(--white)}
.contact-list{left:18px;top:441px;font-size:23px;font-weight:300;color:var(--navy);line-height:31px}
.contact-list div{display:flex;align-items:center;gap:8px}

.offer{left:360px;width:270px;text-align:center}
.back-mark{left:465px;top:30px;width:60px;height:60px;border-radius:50%;background:var(--navy)}
.back-name{top:104px;font-family:"Montserrat",sans-serif;font-weight:800;font-size:14.5px;color:var(--navy)}
.percent{top:144px;font-size:72px;line-height:1;font-weight:800;color:var(--orange);letter-spacing:-3px}
.coupon{top:218px;font-size:25px;font-weight:700;color:var(--navy);line-height:1}
.supplies{top:249px;font-size:21px;font-weight:300;color:var(--deep);line-height:1}
.product{top:288px;font-size:31px;font-weight:700;color:var(--mid);line-height:1;letter-spacing:-.5px}
.product-sub{top:318px;font-size:10.8px;font-weight:700;color:var(--navy)}
.product-by{top:335px;font-size:8.6px;font-weight:400;color:var(--navy)}
.no-salt{top:446px;font-family:"Kanit",sans-serif;font-size:15px;font-weight:600;color:var(--white);line-height:18px;
  text-shadow:1px 0 var(--navy),-1px 0 var(--navy),0 1px var(--navy),0 -1px var(--navy),1px 1px var(--navy),-1px -1px var(--navy),1px -1px var(--navy),-1px 1px var(--navy)}
.risk{top:464px;font-family:"Kanit",sans-serif;font-size:34px;font-weight:700;color:var(--navy);letter-spacing:-1.8px;line-height:1.1}
</style>
</head>
<body>

<section class="card card--front">
  <svg class="bg" width="652" height="521" viewBox="0 0 652 521">
    <defs>
      <linearGradient id="skyWater" x1="0" y1="0" x2="0" y2="1">
        <stop offset="0" stop-color="#2a9fd6"/>
        <stop offset=".25" stop-color="#e8f6fd"/>
        <stop offset=".55" stop-color="#f6fbfe"/>
        <stop offset=".8" stop-color="#7cc3e6"/>
        <stop offset="1" stop-color="#3d93c4"/>
      </linearGradient>
      <linearGradient id="frontBlue" x1="0" y1="0" x2="1" y2="0">
        <stop offset="0" stop-color="#24659c"/>
        <stop offset="1" stop-color="#3a9cc8"/>
      </linearGradient>
    </defs>
    <rect width="652" height="400" fill="url(#skyWater)" role="img" aria-label="Photo of bright sky with clouds above a splashing clear water surface"/>
    <path d="M0,298 C120,350 250,358 360,335 C470,312 560,252 652,250 L652,521 L0,521 Z" fill="#ffffff"/>
    <path d="M0,326 C120,376 250,384 360,362 C470,340 560,290 652,282 L652,521 L0,521 Z" fill="url(#frontBlue)"/>
    <path d="M0,298 C120,350 250,358 360,335 C470,312 560,252 652,250 L652,270 C560,274 470,330 360,352 C250,374 120,366 0,318 Z" fill="var(--orange)"/>
  </svg>

  <div class="brand-mark"></div>
  <div class="abs center brand-name">TARNELL PURE SYSTEMS</div>

  <div class="abs indicia">
    <div class="top">PRSRT STD<br>ECRWSS<br>U.S.POSTAGE<br>PAID<br>EDDM RETAIL</div>
    <div class="bottom">****ECRWSS****<br><br>Local<br>Postal Customer</div>
  </div>

  <h1 class="abs center headline">IS YOUR WATER SAFE?</h1>
  <p class="abs center intro">we are a family-owned business that specializes in providing high quality water filtration systems to residential and<br>commercial properties. We understand how important it is to have safe, clean, and fresh wate</p>

  <div class="abs rule" style="left:0;width:166px"></div>
  <div class="abs rule" style="left:481px;width:171px"></div>
  <div class="abs center concerns">Concerns with your water?</div>

  <div class="abs center contact-row">
    <span>
      <svg width="20" height="20" viewBox="0 0 24 24" aria-hidden="true"><path d="M6.6 2.5l3 3.6-1.9 2.4a13 13 0 0 0 7.8 7.8l2.4-1.9 3.6 3-2.2 3.2C10.8 20.1 3.9 13.2 3.4 4.7z" fill="var(--orange)"/><path d="M14 3a7 7 0 0 1 7 7M14 6.5A3.5 3.5 0 0 1 17.5 10" stroke="var(--orange)" stroke-width="1.8" fill="none"/></svg>
      tarnellpuresystems.com
    </span>
    <span>
      <svg width="20" height="20" viewBox="0 0 24 24" aria-hidden="true"><g fill="none" stroke="var(--orange)" stroke-width="1.8"><circle cx="12" cy="12" r="10"/><ellipse cx="12" cy="12" rx="4.5" ry="10"/><path d="M2 12h20M4 6.5h16M4 17.5h16"/></g></svg>
      555-014-2290
    </span>
  </div>
</section>

<section class="card card--back">
  <svg class="bg" width="652" height="521" viewBox="0 0 652 521">
    <defs>
      <linearGradient id="backDeep" x1="0" y1="0" x2="0" y2="1">
        <stop offset="0" stop-color="#0b4e86"/>
        <stop offset="1" stop-color="#13569a"/>
      </linearGradient>
      <linearGradient id="backLow" x1="0" y1="0" x2="0" y2="1">
        <stop offset="0" stop-color="#1b8fc8"/>
        <stop offset="1" stop-color="#1f92c8"/>
      </linearGradient>
      <linearGradient id="splash" x1="0" y1="0" x2="0" y2="1">
        <stop offset="0" stop-color="#eef8fd"/>
        <stop offset=".35" stop-color="#9dd0ea"/>
        <stop offset=".7" stop-color="#8cc7e6"/>
        <stop offset="1" stop-color="#c4e4f4"/>
      </linearGradient>
    </defs>
    <rect x="370" y="340" width="282" height="181" fill="url(#splash)" role="img" aria-label="Photo of a clear water splash"/>
    <path d="M0,0 L395,0 C342,110 315,210 320,300 C325,400 355,470 372,521 L0,521 Z" fill="#ffffff"/>
    <path d="M390,0 L410,0 C355,110 328,210 333,300 C338,400 366,470 386,521 L358,521 C340,470 312,400 307,300 C302,210 330,110 390,0 Z" fill="var(--orange)"/>
    <path d="M0,0 L364,0 C315,110 298,210 303,300 C308,400 338,470 358,521 L0,521 Z" fill="url(#backDeep)"/>
    <path d="M0,345 C110,330 220,332 316,350 C323,420 342,480 358,521 L0,521 Z" fill="url(#backLow)"/>
  </svg>

  <h2 class="abs lead">Sadly, the water quality<br>in Florida is ranked as<br>the 2nd worst water<br>in the U.S.</h2>
  <div class="abs about-pill">ABOUT US</div>
  <p class="abs about-copy">At Tarnell Pure Systems, we are a family-owned<br>business that specializes in providing high quality<br>water filtration systems to residential and<br>commercial properties. We understand how<br>important it is to have safe, clean, and fresh water.<br>That’s why we offer the Alkaline Clearvane CV8 water<br>iltration system. We strive to be honest and<br>reliable, providing our customers with pure, quality<br>water filtration solutions&nbsp; hat they can trust.</p>
  <p class="abs leader">For The Past 6 Years In A Row The Clearvane<br>Pro Whole House Water Filter, Water<br>Purification and Water softeners have been<br>the leader in the water treatment Industry</p>

  <div class="abs contact-list">
    <div>
      <svg width="20" height="20" viewBox="0 0 24 24" aria-hidden="true"><path d="M6.6 2.5l3 3.6-1.9 2.4a13 13 0 0 0 7.8 7.8l2.4-1.9 3.6 3-2.2 3.2C10.8 20.1 3.9 13.2 3.4 4.7z" fill="var(--navy)"/><path d="M14 3a7 7 0 0 1 7 7M14 6.5A3.5 3.5 0 0 1 17.5 10" stroke="var(--navy)" stroke-width="1.8" fill="none"/></svg>
      tarnellpuresystems.com
    </div>
    <div>
      <svg width="24" height="24" viewBox="0 0 24 24" aria-hidden="true"><g fill="none" stroke="var(--navy)" stroke-width="1.8"><circle cx="12" cy="12" r="10"/><ellipse cx="12" cy="12" rx="4.5" ry="10"/><path d="M2 12h20M4 6.5h16M4 17.5h16"/></g></svg>
      555-014-2290
    </div>
  </div>

  <div class="abs back-mark"></div>
  <div class="abs offer back-name">TARNELL PURE SYSTEMS</div>
  <div class="abs offer percent">15% off</div>
  <div class="abs offer coupon">Coupon Code 3916</div>
  <div class="abs offer supplies">While Supplies Last</div>
  <div class="abs offer product">Clearvane Pro</div>
  <div class="abs offer product-sub">Whole Home Water Filter/Softener</div>
  <div class="abs offer product-by">By: Quellarobrook Guild</div>
  <div class="abs offer no-salt">No Salt, No Discharge of Water</div>
  <div class="abs offer risk">Don't Be At Risk</div>
</section>

</body>
</html>
```